Business card for a new cabinet shop company named Veloran Cabinets for high end cabinets

Design a business card, thinking dark rich green with colours to speak of high end luxury ie; cream, gold, black possibly

Mitchell Tarrowby
Director Craftsman
Email: info@veloranjoinery-example.com.au
Instagram : @veloran.cabinets

```html
<!DOCTYPE html>
<html lang="en">
<head>
<meta charset="utf-8">
<title>Veloran Cabinets — Business Card</title>
<link href="https://fonts.googleapis.com/css2?family=Montserrat:wght@400;500;700&display=swap" rel="stylesheet">
<style>
  :root {
    --backdrop: #1c1c1c;
    --card-green: #071c10;
    --card-green-deep: #05160c;
    --accent-green: #1f8a45;
    --accent-green-soft: rgba(31, 138, 69, 0.55);
    --gold: #c9a862;
    --gold-soft: rgba(201, 168, 98, 0.55);
    --muted: #9a9a8f;
  }
  * { box-sizing: border-box; margin: 0; padding: 0; }
  html, body {
    width: 1200px; height: 875px; overflow: hidden;
    background: radial-gradient(ellipse at 50% 45%, #2e2e2e 0%, var(--backdrop) 70%);
    font-family: "Montserrat", sans-serif;
  }
  .stage {
    width: 1200px; height: 875px;
    display: flex; align-items: center; justify-content: center; gap: 48px;
  }
  .card {
    position: relative;
    width: 540px; height: 309px;
    border-radius: 20px;
    background: linear-gradient(135deg, var(--card-green) 0%, var(--card-green-deep) 100%);
    border: 1px solid var(--gold);
    box-shadow: 0 24px 50px rgba(0,0,0,0.55);
    overflow: hidden;
  }
  /* Decorative emblem areas, kept as soft tonal fields */
  .emblem-field {
    position: absolute;
    pointer-events: none;
  }
  .card-front .emblem-field {
    right: 0; top: 0; width: 270px; height: 100%;
    background:
      radial-gradient(ellipse 55% 45% at 30% 22%, var(--gold-soft) 0%, rgba(201,168,98,0) 70%),
      radial-gradient(ellipse 65% 50% at 75% 70%, var(--accent-green-soft) 0%, rgba(31,138,69,0) 72%);
  }
  .card-back .emblem-field {
    left: 0; top: 0; width: 230px; height: 100%;
    background:
      radial-gradient(ellipse 50% 30% at 25% 10%, var(--gold-soft) 0%, rgba(201,168,98,0) 70%),
      radial-gradient(ellipse 60% 60% at 55% 65%, var(--accent-green-soft) 0%, rgba(31,138,69,0) 72%);
  }
  /* Front */
  .card-front .identity {
    position: absolute; left: 40px; bottom: 42px;
  }
  .person-name {
    color: var(--gold); font-weight: 700; font-size: 24px; letter-spacing: 0.5px;
    text-transform: uppercase;
  }
  .person-role {
    color: var(--muted); font-weight: 400; font-size: 15px; margin-top: 4px; letter-spacing: 0.4px;
  }
  .divider {
    width: 56px; height: 1.5px; background: var(--gold); margin: 14px 0 14px;
  }
  .contact-list { list-style: none; }
  .contact-item {
    display: flex; align-items: center; gap: 10px;
    color: var(--muted); font-size: 13px; line-height: 1.9; letter-spacing: 0.3px;
  }
  .contact-icon { width: 14px; height: 14px; flex: none; }
  /* Back */
  .card-back .wordmark {
    position: absolute; right: 40px; top: 50%; transform: translateY(-50%);
    display: flex; align-items: center; gap: 14px;
  }
  .wordmark-dot {
    width: 18px; height: 18px; border-radius: 50%; background: var(--gold); flex: none;
  }
  .wordmark-name {
    color: var(--gold); font-weight: 500; font-size: 28px; letter-spacing: 1px; white-space: nowrap;
  }
</style>
</head>
<body>
<main class="stage">
  <section class="card card-front" aria-label="Business card front">
    <div class="emblem-field" role="img" aria-label="Large gold and green geometric line emblem decoration"></div>
    <div class="identity">
      <h1 class="person-name">Mitchell Tarrowby</h1>
      <p class="person-role">Director Craftsman</p>
      <div class="divider"></div>
      <ul class="contact-list">
        <li class="contact-item">
          <svg class="contact-icon" viewBox="0 0 14 14" aria-hidden="true">
            <rect x="1" y="3" width="12" height="8" fill="var(--gold)"/>
            <path d="M1 3 L7 8 L13 3" fill="none" stroke="var(--card-green)" stroke-width="1.2"/>
          </svg>
          info@veloranjoinery-example.com.au
        </li>
        <li class="contact-item">
          <svg class="contact-icon" viewBox="0 0 14 14" aria-hidden="true">
            <rect x="1.5" y="1.5" width="11" height="11" rx="2" fill="none" stroke="var(--gold)" stroke-width="1.4"/>
          </svg>
          @veloran.cabinets
        </li>
      </ul>
    </div>
  </section>

  <section class="card card-back" aria-label="Business card back">
    <div class="emblem-field" role="img" aria-label="Cropped gold and green geometric line emblem decoration"></div>
    <div class="wordmark">
      <span class="wordmark-dot" aria-hidden="true"></span>
      <span class="wordmark-name">Veloran Cabinets</span>
    </div>
  </section>
</main>
</body>
</html>
```